Business Card Design

We need a business card designed for our new company. Prefer a black card with white logo & writing.

Contact Information for Business Card

Ted Galloway, address: 7-4812 Fernhollow Road, Abbotsford, BC, V3K 8R2, Office Phone: 604-712-3390, Cell: 604-947-2164, Email: ted@resinworkshub.ca

Colors

Designer to choose only greyscale colors for use in the design.

```html
<!DOCTYPE html>
<html lang="en">
<head>
<meta charset="utf-8">
<title>Resinworks Hub – Business Card</title>
<link href="https://fonts.googleapis.com/css2?family=Poppins:wght@400;600;800&display=swap" rel="stylesheet">
<style>
  :root {
    --canvas: #2b2a2a;
    --card: #1c1817;
    --ink: #ffffff;
    --rule: #6b6767;
    --band: #4a4646;
    --band-light: #6e6a6a;
  }
  * { margin: 0; padding: 0; box-sizing: border-box; }
  html, body { width: 1200px; height: 866px; overflow: hidden; }
  body {
    background: var(--canvas);
    font-family: "Poppins", sans-serif;
    color: var(--ink);
    display: flex;
    flex-direction: column;
    align-items: center;
    justify-content: center;
    gap: 44px;
  }
  .card {
    position: relative;
    width: 620px;
    height: 354px;
    background: var(--card);
    overflow: hidden;
    box-shadow: 0 10px 26px rgba(0,0,0,.45);
  }
  .brand {
    display: flex;
    align-items: center;
    gap: 12px;
    font-weight: 800;
    letter-spacing: .5px;
    text-transform: uppercase;
    white-space: nowrap;
  }
  .brand-dot {
    border: 3px solid var(--ink);
    border-radius: 50%;
    flex: none;
  }
  .card-back { display: flex; align-items: center; justify-content: center; }
  .card-back .brand { font-size: 44px; }
  .card-back .brand-dot { width: 40px; height: 40px; }

  .holder-name {
    position: absolute; left: 44px; top: 44px;
    font-size: 19px; font-weight: 600; text-transform: uppercase; letter-spacing: .3px;
  }
  .divider {
    position: absolute; left: 30px; top: 112px;
    width: 540px; height: 1px; background: var(--rule);
    transform: rotate(13deg); transform-origin: left center;
  }
  .contact-list {
    position: absolute; left: 34px; top: 150px;
    list-style: none; font-size: 15px; line-height: 22px;
  }
  .contact-list li { display: flex; align-items: center; gap: 8px; }
  .contact-list svg { width: 14px; height: 14px; fill: none; stroke: var(--ink); stroke-width: 1.6; }
  .card-front .brand { position: absolute; right: 40px; top: 150px; font-size: 28px; }
  .card-front .brand-dot { width: 26px; height: 26px; }
  .address {
    position: absolute; right: 40px; bottom: 44px;
    font-size: 16px; line-height: 22px; text-align: right;
  }
  .base-band { position: absolute; left: 0; bottom: 0; width: 620px; height: 40px; }
</style>
</head>
<body>
  <section class="card card-back" aria-label="Card back">
    <div class="brand"><span class="brand-dot"></span>Resinworks Hub</div>
  </section>

  <section class="card card-front" aria-label="Card front">
    <h1 class="holder-name">Ted Galloway</h1>
    <div class="divider"></div>
    <ul class="contact-list">
      <li><svg viewBox="0 0 14 14"><path d="M3 1.5l2.2 2.4-1.2 1.6c.8 1.8 2.1 3.1 3.9 3.9l1.6-1.2 2.4 2.2-1.4 2C6 12 2 8 1.1 2.9z"/></svg>604-712-3390</li>
      <li><svg viewBox="0 0 14 14"><rect x="3.5" y="1" width="7" height="12" rx="1.2"/><path d="M6 11h2"/></svg>604-947-2164</li>
      <li><svg viewBox="0 0 14 14"><rect x="1" y="3" width="12" height="8"/><path d="M1 3l6 5 6-5"/></svg>ted@resinworkshub.ca</li>
    </ul>
    <div class="brand"><span class="brand-dot"></span>Resinworks Hub</div>
    <p class="address">7-4812 Fernhollow Road<br>Abbotsford, BC, V3K 8R2</p>
    <svg class="base-band" viewBox="0 0 620 40" preserveAspectRatio="none" aria-hidden="true">
      <path d="M0 28 H250 C275 28 280 16 305 16 H620 V40 H0 Z" fill="var(--band)"/>
      <path d="M0 28 H250 C262 28 268 24 274 20 L250 31 H0 Z" fill="var(--band-light)"/>
    </svg>
  </section>
</body>
</html>
```